Logo/ business card idea for a weld inspection/ nondestructive testing LLC

I have just started an LLC (my first) for weld inspection and non-destructive testing. I am the president and only member of this company. It is a very niche industry and word of mouth is basically the only advertisement needed to get you the next job. I will offer magnetic particle, dye penetrant, ultrasonic, and visual testing for the non-destructive services. X-ray is a form of non-destructive testing that I spent a few years doing but to costly for me at this time. All pipelines under the ground are welded, visually inspected and x-ray by someone just like me. All new building construction, any type of nuclear plant , pressure vessel, ect. , the welds are inspected by someone like me. Its is every increasing also with safety concerns. People are living right next to this stuff!!I will be the guy that fabrication shops or construction companies call to give the final OK that the welds are satisfactory after inspection to a certain code or standard. The designers have all the freedom they wish but I have attached a PDF with greater explanations and color ideas. I want raised glossy print on the front of the card and the necessary info. The back will not have raised print and serve more as a brief resume listing the certifications I have. The company only cares about the certifications and ultimately my signature. I want to make the front of the car into a fridge magnet to pass out with the card also. Something that is appealing to hang up instead of getting lost in someones wallet. The final design………. should be classic and stand the test of time. It should communicate precision and accuracy as well as incorporate the sound beam you will find in the PDF I’ve attached.Thanks and have a great day,Wade

Target Market(s)

Adult males in english speaking countries that handle welding and/or construction duties. Most of the time under heavy time constraints and deadlines. Ages 30-60

Industry/Entity Type

Construction

Contact Information for Business Card

Danbury Inspection Services, LLC
Wade Hollister
Ithaca, MI
989-472-5130
hollw7ds@mailbrook.net

Font styles to use
Other font styles liked:
• designers choice

Requirements
Nice to have
• The logo on the front can completely encase the Danbury, be segmented incorporating the Danbury, or next to it. There can also be a couple of “flaws” (the red, blue and yellow in some of the pictures attached in the PDF) in the sound beam spread.

```html
<!DOCTYPE html>
<html lang="en">
<head>
<meta charset="utf-8">
<title>Danbury Inspection Services – Business Card</title>
<link href="https://fonts.googleapis.com/css2?family=Mulish:wght@200;300;400&display=swap" rel="stylesheet">
<style>
  :root {
    --backdrop: #b4b4b4;
    --card-front: #ececec;
    --card-front-edge: #f7f7f7;
    --brand-orange: #e8652a;
    --orange-light: #fa7d3e;
    --orange-deep: #cb4711;
    --text-grey: #6b6b6b;
    --text-dark: #464646;
    --white: #ffffff;
  }
  * { box-sizing: border-box; margin: 0; padding: 0; }
  html, body {
    width: 1200px; height: 1000px; overflow: hidden;
    background: radial-gradient(ellipse at 50% 45%, #c9c9c9 0%, var(--backdrop) 70%);
    font-family: "Mulish", "Avenir Next", sans-serif;
  }
  .canvas { position: relative; width: 1200px; height: 1000px; }
  .card {
    position: absolute; width: 680px; height: 390px;
    box-shadow: 0 6px 14px rgba(0,0,0,0.25);
  }
  .card-front {
    left: 90px; top: 110px;
    background: linear-gradient(160deg, #dcdcdc 0%, var(--card-front) 45%, var(--card-front-edge) 100%);
  }
  .brand-name {
    position: absolute; left: 190px; top: 92px;
    font-size: 92px; font-weight: 200; color: var(--brand-orange);
    letter-spacing: 1px; line-height: 1;
  }
  .brand-tagline {
    position: absolute; left: 200px; top: 205px;
    font-size: 24px; font-weight: 300; color: var(--text-grey);
  }
  .contact-line {
    position: absolute; left: 58px; bottom: 34px;
    font-size: 21px; font-weight: 400; color: var(--text-dark);
    letter-spacing: 0.5px; white-space: nowrap;
  }
  .contact-line .sep { margin: 0 10px; }

  .card-back {
    left: 430px; top: 520px;
    background: linear-gradient(150deg, var(--orange-light) 0%, #e8622a 50%, var(--orange-deep) 100%);
    color: var(--white);
  }
  .cert-group { position: absolute; display: flex; align-items: center; }
  .cert-group.body { top: 72px; left: 160px; }
  .cert-group.level { top: 178px; left: 42px; }
  .cert-heading { font-weight: 300; line-height: 1; letter-spacing: 1px; }
  .body .cert-heading { font-size: 80px; }
  .level .cert-heading { font-size: 84px; }
  .cert-list { list-style: none; margin-left: 16px; font-size: 18px; font-weight: 400; line-height: 1.15; letter-spacing: 0.5px; }
</style>
</head>
<body>
<main class="canvas">
  <section class="card card-front" aria-label="Business card front">
    <div class="brand-name">Danbury</div>
    <div class="brand-tagline">Inspection Services, LLC</div>
    <p class="contact-line">Wade Hollister<span class="sep">|</span>(989) 472-5130<span class="sep">|</span>hollw7ds@mailbrook.net</p>
  </section>

  <section class="card card-back" aria-label="Business card back">
    <div class="cert-group body">
      <span class="cert-heading">WQS</span>
      <ul class="cert-list">
        <li>Certified Welding Inspector</li>
        <li>Certified Radiographic Interpreter</li>
        <li>Certified Welding Educator</li>
      </ul>
    </div>
    <div class="cert-group level">
      <span class="cert-heading">LEVEL II</span>
      <ul class="cert-list">
        <li>Ultrasonic Testing</li>
        <li>Magnetic Particle Testing</li>
        <li>Liquid Penetrant Testing</li>
      </ul>
    </div>
  </section>
</main>
</body>
</html>
```